Dental specialist needs a sharp looking letterhead

I am looking for a letterhead to be used to send letters and communication between myself (a dental specialist) and other dentists.
My office is a state of the art dental specialty office.
I need to letterhead to also state:
Bertram L. Oswick DDS
2748 Tollard Avenue, Suite K
West Tollard, NY 14391
(716)392-5061
fax: (716)392-5087
oswickroot.com (**this email address may change)

i included my logo designs.
thank you

Target Market(s)

dentists

Industry/Entity Type

Communication

Requirements
Must have
• the included logo, whether the vertical or horizontal versions

```html
<!DOCTYPE html>
<html lang="en">
<head>
<meta charset="utf-8">
<title>Keystone Endodontics P.C. — Letterhead</title>
<link rel="stylesheet" href="https://fonts.googleapis.com/css2?family=Merriweather:wght@400;700&family=Lato:wght@400;700&display=swap">
<style>
  :root {
    --backdrop: #ececec;
    --paper: #ffffff;
    --brand-blue: #3a8fd0;
    --brand-green: #7db526;
    --ink: #222222;
    --ink-soft: #555555;
    --on-band: #ffffff;
  }
  * { margin: 0; padding: 0; box-sizing: border-box; }
  html, body {
    width: 1200px;
    height: 968px;
    overflow: hidden;
    background: var(--backdrop);
  }
  .letterhead {
    position: absolute;
    left: 282px;
    top: 34px;
    width: 636px;
    height: 900px;
    background: var(--paper);
    box-shadow: 0 2px 10px rgba(0,0,0,0.08);
  }
  .brand {
    position: absolute;
    left: 150px;
    top: 62px;
    display: flex;
    align-items: center;
    gap: 10px;
  }
  .brand-dot {
    width: 30px;
    height: 30px;
    border-radius: 50%;
    background: var(--brand-blue);
  }
  .brand-name {
    font-family: "Merriweather", serif;
    font-weight: 700;
    font-size: 17px;
    line-height: 1.15;
    color: var(--ink);
    letter-spacing: 0.02em;
  }
  .contact-band {
    position: absolute;
    left: 0;
    top: 122px;
    width: 100%;
    height: 22px;
    display: flex;
  }
  .band-name {
    width: 150px;
    background: var(--brand-blue);
    color: var(--on-band);
    font-family: "Merriweather", serif;
    font-size: 10px;
    display: flex;
    align-items: center;
    justify-content: flex-end;
    padding-right: 8px;
    white-space: nowrap;
  }
  .band-details {
    flex: 1;
    background: var(--brand-green);
    color: var(--on-band);
    font-family: "Lato", sans-serif;
    font-size: 8.5px;
    display: flex;
    align-items: center;
    gap: 16px;
    padding-left: 12px;
  }
  .detail {
    display: flex;
    align-items: center;
    gap: 4px;
    white-space: nowrap;
  }
  .detail svg { width: 9px; height: 9px; }
  .footer {
    position: absolute;
    right: 36px;
    bottom: 46px;
    width: 330px;
  }
  .address {
    font-family: "Lato", sans-serif;
    font-size: 9px;
    color: var(--ink);
    display: flex;
    align-items: center;
    justify-content: flex-end;
    gap: 4px;
    margin-bottom: 6px;
  }
  .address svg { width: 10px; height: 10px; }
  .rule { height: 1px; }
  .rule-blue { background: var(--brand-blue); width: 310px; margin-left: 0; }
  .rule-green { background: var(--brand-green); width: 310px; margin-left: 20px; margin-top: 6px; }
</style>
</head>
<body>
  <main class="letterhead">
    <div class="brand">
      <span class="brand-dot"></span>
      <span class="brand-name">Keystone Endodontics P.C.</span>
    </div>

    <div class="contact-band">
      <div class="band-name">Bertram L. Oswick DDS</div>
      <div class="band-details">
        <span class="detail">
          <svg viewBox="0 0 10 10"><circle cx="5" cy="5" r="5" fill="#1f3d0a"/><path d="M3.2 2.6l1 1-.5.7c.4.7.9 1.2 1.6 1.6l.7-.5 1 1-.6.8C4.6 7.1 2.9 5.4 2.4 3.2z" fill="#fff"/></svg>
          (716)392-5061
        </span>
        <span class="detail">
          <svg viewBox="0 0 10 10"><circle cx="5" cy="5" r="5" fill="#1f3d0a"/><rect x="3" y="2.3" width="4" height="2" fill="#fff"/><rect x="2.2" y="4.5" width="5.6" height="2.2" fill="#fff"/><rect x="3" y="6.9" width="4" height="1" fill="#fff"/></svg>
          (716)392-5087
        </span>
        <span class="detail">
          <svg viewBox="0 0 10 10"><circle cx="5" cy="5" r="5" fill="#1f3d0a"/><rect x="2.3" y="3.2" width="5.4" height="3.6" fill="#fff"/><path d="M2.3 3.2L5 5.3l2.7-2.1" stroke="#1f3d0a" stroke-width="0.6" fill="none"/></svg>
          bertram@oswickroot.com
        </span>
      </div>
    </div>

    <footer class="footer">
      <p class="address">
        <svg viewBox="0 0 10 10"><circle cx="5" cy="5" r="5" fill="#222"/><path d="M5 2a1.8 1.8 0 0 1 1.8 1.8C6.8 5.2 5 7.8 5 7.8S3.2 5.2 3.2 3.8A1.8 1.8 0 0 1 5 2z" fill="#fff"/><circle cx="5" cy="3.8" r="0.6" fill="#222"/></svg>
        2748 Tollard Avenue, Suite K West Tollard, NY 14391
      </p>
      <div class="rule rule-blue"></div>
      <div class="rule rule-green"></div>
    </footer>
  </main>
</body>
</html>
```